New banner graphics for Tondix.com website

I've developed a software tool that helps businesses ensure they are working on their most valuable and important work.

I would like a banner graphic for my home page (www.tondix.com) that can somehow capture the value of focus and intentional outcomes.

I had an initial thought of a starry sky that shifts focus to a few bright stars, but while that might sound ok, I think my idea is lame hence I'm coming to you guys.

My sites two primary colors are a soft purple and gray.
#919EC1(purple)
#9E9E9E (gray)

Target Market(s)

B2B for enterprises. Typical customers are CFOs, CIOs/Heads of IT

Industry/Entity Type

Business Software

Number of Pages Required

1 page

Font styles to use
Sans Serif

Colors
b8a6cd
cedeed

Requirements
Must have
• I use Divi as my Wordpress theme and the current main landing page can be seen at www.tondix.com.
• My logo colors are:
• #919EC1(purple)
• #9E9E9E (gray)
Should not have
• Lots of distraction or visual "noise". I want to re-enforce the message that my software is focused on their business and not my products or website.

```html
<!DOCTYPE html>
<html lang="en">
<head>
<meta charset="utf-8">
<title>Tondix – Waypoint</title>
<link href="https://fonts.googleapis.com/css2?family=Nunito:wght@400;600&family=Open+Sans:ital,wght@0,400;0,600;1,400&family=Oswald:wght@400&display=swap" rel="stylesheet">
<style>
:root{
  --purple:#b8a6cd;
  --purple-deep:#919ec1;
  --soft-blue:#cedeed;
  --gray:#9e9e9e;
  --ink:#222;
  --text:#555;
  --muted:#777;
  --panel:#f4f4f4;
  --footer:#111;
  --footer-base:#0a0a0a;
  --white:#fff;
}
*{margin:0;padding:0;box-sizing:border-box}
html,body{width:1200px;height:2899px;overflow:hidden}
body{position:relative;background:var(--white);font-family:"Open Sans",sans-serif;color:var(--text)}
.abs{position:absolute}
.center{left:0;width:1200px;text-align:center}

/* header */
.site-header{top:0;left:0;width:1200px;height:110px;background:var(--white)}
.btn-demo{left:95px;top:37px;width:170px;height:35px;border:2px solid var(--purple);border-radius:18px;color:var(--purple);font:400 14px "Nunito",sans-serif;display:flex;align-items:center;justify-content:center}
.nav-link{top:45px;font:400 15px "Nunito",sans-serif;color:var(--ink)}
.brand{left:480px;top:24px;width:240px;text-align:center;font:400 48px "Nunito",sans-serif;color:var(--purple-deep);letter-spacing:1px}
.tool-dot{top:39px;width:28px;height:28px;border-radius:50%}
.social{width:22px;height:22px;border-radius:4px;background:#333}

/* hero */
.hero{top:110px;left:0;width:1200px;height:543px;background:linear-gradient(180deg,#1c2136 0%,#3a4574 35%,#5b5f8f 60%,#3d3e5c 78%,#0a0a0e 88%,#050505 100%)}
.hero-title{top:310px;font:400 45px "Oswald",sans-serif;color:var(--white)}
.hero-sub{top:378px;font:400 19px "Open Sans",sans-serif;color:var(--white)}
.hero-arrow{top:533px;width:28px;height:28px;border-radius:50%;background:rgba(255,255,255,.25)}

/* intro */
.section-title{font:400 27px "Nunito",sans-serif;color:var(--ink);letter-spacing:.5px}
.intro-lead{top:764px;font:400 20px "Open Sans",sans-serif;color:#444}
.intro-body{top:800px;font:400 16px/29px "Open Sans",sans-serif;color:var(--muted)}
.feature{width:240px;text-align:center}
.feature-circle{width:104px;height:104px;border-radius:50%;background:var(--purple);margin:0 auto;display:flex;align-items:center;justify-content:center}
.feature-label{margin-top:26px;font:400 13px "Nunito",sans-serif;color:var(--ink);letter-spacing:.3px}
.intro-close{top:1099px;font:400 19px "Open Sans",sans-serif;color:#555}
.btn-start{width:156px;height:42px;border-radius:21px;background:var(--soft-blue);color:var(--ink);font:400 14px "Nunito",sans-serif;display:flex;align-items:center;justify-content:center;left:522px}

/* about */
.about-photo{top:1265px;left:0;width:578px;height:375px;background:radial-gradient(circle at 50% 85%,#e8a050 0%,#8a5a44 18%,#3b3f5e 45%,#15182a 80%)}
.about-panel{top:1265px;left:578px;width:622px;height:375px;background:var(--panel)}
.about-kicker{left:624px;top:1322px;font:400 23px "Nunito",sans-serif;color:#333}
.about-title{left:624px;top:1349px;font:400 30px "Nunito",sans-serif;color:#333}
.about-text{left:624px;top:1400px;width:530px;font:400 13.5px/25px "Open Sans",sans-serif;color:#555;text-align:justify}
.btn-read{left:624px;top:1542px;width:104px;height:31px;border-radius:16px;background:var(--purple);color:var(--white);font:400 12px "Nunito",sans-serif;display:flex;align-items:center;justify-content:center}

/* differences */
.diff{width:500px;display:flex;gap:22px}
.diff-icon{flex:none;width:94px;height:94px;border:1.5px solid #555;border-radius:50%;display:flex;align-items:center;justify-content:center}
.diff-title{margin-top:10px;font:400 17px "Nunito",sans-serif;color:var(--ink)}
.diff-text{margin-top:6px;font:400 12.5px/21px "Open Sans",sans-serif;color:var(--muted)}

/* testimonial */
.testimonials{top:2216px;left:0;width:1200px;height:379px;background:#f5f5f5}
.avatar{left:553px;top:2336px;width:92px;height:92px;border-radius:50%;background:linear-gradient(160deg,#d9d9d9,#b8b0a8)}
.quote{top:2452px;font:400 17px/26px "Open Sans",sans-serif;color:#444}
.quote-author{top:2518px;font:italic 400 16px "Open Sans",sans-serif;color:#444}

/* footer */
.site-footer{top:2595px;left:0;width:1200px;height:220px;background:var(--footer)}
.footer-brand{left:87px;top:2686px;font:400 46px "Nunito",sans-serif;color:var(--white)}
.footer-title{top:2645px;font:400 15px "Nunito",sans-serif;color:var(--white);letter-spacing:.3px}
.footer-text{font:400 11.5px/24px "Open Sans",sans-serif;color:#ddd}
.news-input{left:655px;top:2725px;width:150px;height:30px;background:var(--white);font:400 11px "Open Sans",sans-serif;color:#888;padding:8px 6px}
.news-submit{left:805px;top:2725px;width:54px;height:30px;background:var(--purple);color:var(--white);font:400 11px "Open Sans",sans-serif;display:flex;align-items:center;justify-content:center}
.footer-social{width:24px;height:24px;border-radius:4px;background:var(--white);top:2691px}
.footer-base{top:2815px;left:0;width:1200px;height:84px;background:var(--footer-base)}
.copyright{top:2855px;font:400 13px "Open Sans",sans-serif;color:var(--white)}
</style>
</head>
<body>

<header class="site-header abs">
  <div class="btn-demo abs">REQUEST A DEMO</div>
  <div class="nav-link abs" style="left:286px">LINKS</div>
  <div class="nav-link abs" style="left:373px">START NOW</div>
  <div class="brand abs">Tondix</div>
  <div class="tool-dot abs" style="left:900px;background:var(--soft-blue)">
    <svg width="28" height="28" viewBox="0 0 28 28"><circle cx="13" cy="13" r="5" fill="none" stroke="#fff" stroke-width="2"/><line x1="17" y1="17" x2="21" y2="21" stroke="#fff" stroke-width="2"/></svg>
  </div>
  <div class="tool-dot abs" style="left:935px;background:var(--purple)">
    <svg width="28" height="28" viewBox="0 0 28 28"><path d="M10 8c1 0 2 3 2 4s-1 1-1 2 2 3 3 3 1-1 2-1 4 1 4 2-1 3-3 3C12 21 7 16 7 11c0-2 2-3 3-3z" fill="#fff"/></svg>
  </div>
  <div class="social abs" style="left:985px;top:39px"></div>
  <div class="social abs" style="left:1020px;top:39px"></div>
  <div class="social abs" style="left:1055px;top:39px"></div>
  <div class="social abs" style="left:1090px;top:39px"></div>
</header>

<section class="hero abs" role="img" aria-label="Night sky full of stars over a dark mountain silhouette with a warm glow on the horizon"></section>
<h1 class="hero-title abs center">IS YOUR BUSINESS STRATEGY</h1>
<p class="hero-sub abs center">WRITTEN DOWN or LOOSE THOUGHTS – ON THE BEST OF DAYS.</p>
<div class="hero-arrow abs" style="left:1051px"><svg width="28" height="28" viewBox="0 0 28 28"><path d="M16 9l-5 5 5 5" fill="none" stroke="#fff" stroke-width="2"/></svg></div>
<div class="hero-arrow abs" style="left:1085px"><svg width="28" height="28" viewBox="0 0 28 28"><path d="M12 9l5 5-5 5" fill="none" stroke="#fff" stroke-width="2"/></svg></div>

<h2 class="section-title abs center" style="top:722px">GET WAYPOINT</h2>
<p class="intro-lead abs center">A simple software tool that makes your business goals actionable.</p>
<p class="intro-body abs center">Even if you've never felt comfortable defining your business strategy, Waypoint is for you.&nbsp; It's simple to use,<br>easy to understand, and keeps you focused on outcomes.</p>

<div class="feature abs" style="left:120px;top:902px">
  <div class="feature-circle"><svg width="30" height="30" viewBox="0 0 30 30"><circle cx="15" cy="15" r="9" fill="none" stroke="#fff" stroke-width="5" stroke-dasharray="4 3"/><circle cx="15" cy="15" r="6" fill="#fff"/><circle cx="15" cy="15" r="2.5" fill="#b8a6cd"/></svg></div>
  <div class="feature-label">DEFINE THE OUTCOMES</div>
</div>
<div class="feature abs" style="left:371px;top:902px">
  <div class="feature-circle"><svg width="40" height="32" viewBox="0 0 40 32"><circle cx="20" cy="9" r="5" fill="#fff"/><circle cx="10" cy="12" r="4" fill="#fff"/><circle cx="30" cy="12" r="4" fill="#fff"/><path d="M11 28c0-7 4-11 9-11s9 4 9 11z" fill="#fff"/><path d="M3 26c0-5 3-9 7-9 2 0 3 1 4 2-2 2-3 4-3 7z M37 26c0-5-3-9-7-9-2 0-3 1-4 2 2 2 3 4 3 7z" fill="#fff"/></svg></div>
  <div class="feature-label">SET THE DIRECTION</div>
</div>
<div class="feature abs" style="left:614px;top:902px">
  <div class="feature-circle"><svg width="32" height="34" viewBox="0 0 32 34"><rect x="5" y="3" width="14" height="18" fill="#fff"/><path d="M13 11h10l5 5v15H13z" fill="#fff" stroke="#b8a6cd" stroke-width="2"/></svg></div>
  <div class="feature-label">FOCUS THE RESOURCES</div>
</div>
<div class="feature abs" style="left:852px;top:902px">
  <div class="feature-circle"><svg width="30" height="34" viewBox="0 0 30 34"><path d="M15 2l12 4v10c0 8-6 13-12 16C9 29 3 24 3 16V6z" fill="#fff"/><path d="M15 7v20c-4-2-7-6-7-11V9z" fill="#b8a6cd"/></svg></div>
  <div class="feature-label">REDUCE THE RISK</div>
</div>

<p class="intro-close abs center">Be confident that you're focused on your most valuable work.</p>
<div class="btn-start abs" style="top:1151px">START NOW »</div>

<div class="about-photo abs" role="img" aria-label="Silhouette of a lone figure standing on a rock under a glowing galaxy sky"></div>
<div class="about-panel abs"></div>
<div class="about-kicker abs">Tondix</div>
<h2 class="about-title abs">ABOUT US</h2>
<p class="about-text abs">It has survived not only five centuries, but also the leap into electronic typesetting, remaining essentially unchanged. It was popularised in the 1960s with the release of Fontwell sheets containing Lorem Ipsum passages, and more recently with desktop publishing software like Pagecraft Studio including versions of Lorem Ipsum</p>
<div class="btn-read abs">Read More »</div>

<h2 class="section-title abs center" style="top:1740px">WHAT MAKES WAYPOINT DIFFERENT?</h2>

<div class="diff abs" style="left:90px;top:1820px">
  <div class="diff-icon"><svg width="30" height="40" viewBox="0 0 30 40"><rect x="7" y="4" width="16" height="30" rx="2" fill="none" stroke="#b8a6cd" stroke-width="2"/><line x1="7" y1="9" x2="23" y2="9" stroke="#b8a6cd" stroke-width="2"/><line x1="7" y1="28" x2="23" y2="28" stroke="#b8a6cd" stroke-width="2"/></svg></div>
  <div><div class="diff-title">EASE OF USE</div><div class="diff-text">We want you to spend time thinking about and planning for<br>your organization's success, not learning yet another tool.</div></div>
</div>
<div class="diff abs" style="left:650px;top:1822px">
  <div class="diff-icon"><svg width="40" height="36" viewBox="0 0 40 36"><path d="M20 3L4 11h32z" fill="#b8a6cd"/><rect x="8" y="13" width="4" height="14" fill="#b8a6cd"/><rect x="15" y="13" width="4" height="14" fill="#b8a6cd"/><rect x="22" y="13" width="4" height="14" fill="#b8a6cd"/><rect x="29" y="13" width="4" height="14" fill="#b8a6cd"/><rect x="4" y="29" width="32" height="4" fill="#b8a6cd"/></svg></div>
  <div><div class="diff-title">PRACTICAL APPROACH</div><div class="diff-text">Getting started is easier when you aren't worried about an<br>overly sophisticated framework or academic model.</div></div>
</div>
<div class="diff abs" style="left:90px;top:1966px">
  <div class="diff-icon"><svg width="36" height="36" viewBox="0 0 36 36"><rect x="5" y="8" width="22" height="22" rx="2" fill="none" stroke="#b8a6cd" stroke-width="2"/><path d="M14 22l2-6 13-13 4 4-13 13z" fill="none" stroke="#b8a6cd" stroke-width="2"/></svg></div>
  <div><div class="diff-title">FOCUS ON OUTCOMES</div><div class="diff-text">Gain alignment with other leaders and team members early<br>by building, shaping and working towards a shared.</div></div>
</div>
<div class="diff abs" style="left:650px;top:1968px">
  <div class="diff-icon"><svg width="36" height="36" viewBox="0 0 36 36"><rect x="4" y="6" width="16" height="10" rx="5" transform="rotate(45 12 11)" fill="none" stroke="#b8a6cd" stroke-width="3"/><rect x="16" y="20" width="16" height="10" rx="5" transform="rotate(45 24 25)" fill="none" stroke="#b8a6cd" stroke-width="3"/></svg></div>
  <div><div class="diff-title">SUPPORT OF INDUSTRY FRAMEWORKS</div><div class="diff-text">While Waypoint has been designed to be comfortable for all<br>business leaders, it ties well to industry frameworks.</div></div>
</div>

<div class="btn-start abs" style="top:2102px">START NOW »</div>

<section class="testimonials abs"></section>
<h2 class="section-title abs center" style="top:2266px">WHAT PEOPLE ARE SAYING</h2>
<svg class="abs" style="left:500px;top:2370px" width="20" height="26" viewBox="0 0 20 26"><path d="M15 3L5 13l10 10" fill="none" stroke="#888" stroke-width="2.5"/></svg>
<div class="avatar abs" role="img" aria-label="Round portrait of the customer quoted"></div>
<svg class="abs" style="left:680px;top:2370px" width="20" height="26" viewBox="0 0 20 26"><path d="M5 3l10 10L5 23" fill="none" stroke="#888" stroke-width="2.5"/></svg>
<p class="quote abs center">“ Waypoint brings the fanciful world of strategic planning down to earth, and fits<br>practitioners of modern agile management practices ”</p>
<p class="quote-author abs center">Arlen, CEO, IT Services</p>

<footer class="site-footer abs"></footer>
<div class="footer-brand abs">Tondix</div>

<div class="footer-title abs" style="left:356px">CONTACT US</div>
<div class="footer-text abs" style="left:356px;top:2678px">Address : 12 Fernhill Rd, Eastgate<br>Leeds, LS4 2QP<br>Phone : 555-014-2290<br>Email : hello@tondix.com</div>

<div class="footer-title abs" style="left:655px">SIGN UP FOR NEWSLETTER</div>
<div class="footer-text abs" style="left:655px;top:2680px;width:210px;line-height:17px">Your about us information would fit here nicely.</div>
<div class="news-input abs">Email address</div>
<div class="news-submit abs">Submit</div>

<div class="footer-title abs" style="left:947px">FOLLOW US OUT THERE</div>
<div class="footer-social abs" style="left:947px"></div>
<div class="footer-social abs" style="left:985px"></div>
<div class="footer-social abs" style="left:1023px"></div>
<div class="footer-social abs" style="left:1061px"></div>

<div class="footer-base abs"></div>
<p class="copyright abs center">Copyright © 2017. All Rights Reserved</p>

</body>
</html>
```